Cafe Business needs a business card design

I already have an ai logo I would like to use and color. I need someone to make a business card for me on adobe illustrator with it. Its for a cafe restaurant opening in Japan I would like to be able to change out the names, contact info, ect on my own from adobe illustrator.

Industry/Entity Type

Business

Contact Information for Business Card

Double sided with logo on one side and info on the other. Name, Tel, fax, email and west

```html
<!DOCTYPE html>
<html lang="en">
<head>
<meta charset="utf-8">
<title>Sora Tide Cafe — Business Cards</title>
<link rel="stylesheet" href="https://fonts.googleapis.com/css2?family=Jost:wght@700&family=Roboto:wght@300&display=swap">
<style>
  :root {
    --stage: #3b2a21;
    --cafe-blue: #0284e0;
    --cafe-brown: #532c22;
    --paper: #ffffff;
    --ink: #1c1a19;
    --link-blue: #1a8ae0;
  }
  html, body {
    margin: 0;
    padding: 0;
    width: 1200px;
    height: 857px;
    overflow: hidden;
    background: var(--stage);
  }
  .canvas {
    position: relative;
    width: 1200px;
    height: 857px;
  }
  .card {
    position: absolute;
    top: 120px;
    width: 361px;
    height: 615px;
    box-shadow: 0 6px 18px rgba(0, 0, 0, 0.45);
  }
  .card--blue  { left: 38px;  background: var(--cafe-blue); }
  .card--white { left: 419px; background: var(--paper); }
  .card--brown { left: 799px; background: var(--cafe-brown); }

  .brand-mark {
    position: absolute;
    left: 50%;
    transform: translateX(-50%);
  }
  .card--blue .brand-mark,
  .card--brown .brand-mark {
    top: 170px;
    width: 202px;
    height: 197px;
  }
  .card--blue .brand-mark  { background: var(--cafe-brown); }
  .card--brown .brand-mark { background: var(--cafe-blue); }

  .card--white .brand-mark {
    top: 50px;
    width: 118px;
    height: 116px;
    background: var(--ink);
  }

  .brand-name {
    position: absolute;
    left: 0;
    right: 0;
    text-align: center;
    font-family: "Jost", sans-serif;
    font-weight: 700;
    letter-spacing: 1px;
    margin: 0;
    white-space: nowrap;
  }
  .card--blue .brand-name,
  .card--brown .brand-name {
    top: 383px;
    font-size: 38px;
  }
  .card--blue .brand-name  { color: var(--cafe-brown); }
  .card--brown .brand-name { color: var(--cafe-blue); }
  .card--white .brand-name {
    top: 172px;
    font-size: 23px;
    color: var(--ink);
  }

  .contact {
    position: absolute;
    left: 0;
    right: 0;
    top: 452px;
    text-align: center;
    font-family: "Roboto", sans-serif;
    font-weight: 300;
    font-size: 15px;
    color: var(--ink);
    font-style: normal;
    line-height: 20px;
  }
  .contact p { margin: 0; }
  .contact .address { margin-bottom: 6px; }
  .contact .phone   { margin-bottom: 5px; }
  .contact .email   { margin-bottom: 11px; }
  .contact .web     { color: var(--link-blue); }
</style>
</head>
<body>
<main class="canvas">
  <section class="card card--blue" aria-label="Card front, blue">
    <div class="brand-mark"></div>
    <h1 class="brand-name">SORA TIDE CAFE</h1>
  </section>

  <section class="card card--white" aria-label="Card back, contact details">
    <div class="brand-mark"></div>
    <h2 class="brand-name">SORA TIDE CAFE</h2>
    <address class="contact">
      <p class="address">2-14 Minato Lane,<br>Near Hoshimachi Station,<br>Tokyo, Japan</p>
      <p class="phone">P: 808-555-0192</p>
      <p class="email">E: hello@soratidecafe.com</p>
      <p class="web">www.soratidecafe.com</p>
    </address>
  </section>

  <section class="card card--brown" aria-label="Card front, brown">
    <div class="brand-mark"></div>
    <h2 class="brand-name">SORA TIDE CAFE</h2>
  </section>
</main>
</body>
</html>
```